A Brochure to sell LED Downlights to clients

I am starting a campaign on google for LED down lights the link to the landing page can be found at brinholt.com.au/led .

When the client send a contact request i want to be able to send back a brochure of a picture of each light (Approx 6 - 8 types) and have a few sentences on each light and price brake down.

'Quarnel Ostrava 9w LED'

**Information**

1-10 lights $49
11-20 lights $45
21 - 40 lights $42
40 and over $40

EACH LIGHT:

Hi,

This is very good.

I
But,

Each light will have its own price.

Can i get it made like this;

Picture - Spec - Pricing in a table style please? - i like the layout it just need to suit the tables under:

picture - Brand - Price 1-10
Model - Price 11-20
Watts - Price 21-21
lumen - price 30- 40
Warranty = price 40+

Model - Price 11-20
Watts - Price 21-21
lumen - price 30- 40
Warranty = price 40+

Model - Price 11-20
Watts - Price 21-21
lumen - price 30- 40
Warranty = price 40+

and so on....

I want it to be on Microsoft Word so i can easily chop and edit the prices and images also. (So i can print to PDF)

For more information see my website to seek inspiration. I have a zip file of my logo for actual creation and should be also to source pictures of the lights when finalising the design.

brinholt.com.au

Thanks

Added 2 x additional Dimmers please see zip file, same layout/pricing as the downlights

Target Market(s)

Homeowners/commercial business owners

Industry/Entity Type

Electric Company

Font styles to use
Sans Serif

Colors
86cfc6
ffffff
000000

Requirements
Must have
• Professional looking, Colours to the theme of my logo/website
Nice to have
• An awesome design that sells it's self!!!!!!!
• My Logo font is 'Radikil" it would be nice to follow that theme if it doesn't look good i am open to have a nice legible font for the copy.
Should not have
• Cheesy light globes or images

```html
<!DOCTYPE html>
<html lang="en">
<head>
<meta charset="utf-8">
<title>Brinholt Electrical – LED Downlight Catalog 2017-2018</title>
<link href="https://fonts.googleapis.com/css2?family=Josefin+Sans:wght@300;400;600;700&display=swap" rel="stylesheet">
<style>
  :root{
    --stage:#3a3a3a;
    --teal:#00a99d;
    --teal-soft:#86cfc6;
    --ink:#3d3d3d;
    --paper:#ffffff;
    --grid:#2bb0a4;
    --mist:#eef0f0;
    --panel-dark:#3f3f3f;
  }
  *{box-sizing:border-box;margin:0;padding:0}
  html,body{width:1200px;height:2980px;overflow:hidden;background:var(--stage);font-family:"Josefin Sans",sans-serif;color:var(--ink)}
  .page{position:absolute;left:290px;width:622px;background:var(--paper);box-shadow:0 6px 14px rgba(0,0,0,.55);overflow:hidden}

  /* ---------- Cover ---------- */
  .cover{top:99px;height:875px}
  .cover-backdrop{position:absolute;inset:0;background:linear-gradient(180deg,#f4f4f4 0%,#e9eaea 45%,#f3f3f3 100%)}
  .cover-title{position:absolute;right:32px;top:112px;text-align:right;line-height:1}
  .cover-title .word{display:block;font-size:46px;font-weight:400;color:var(--teal);letter-spacing:1px}
  .cover-title .years{display:block;font-size:44px;font-weight:400;color:#4a4a4a;margin-top:6px}
  .tile{position:absolute}
  .tile.dark{left:133px;top:248px;width:175px;height:169px;background:#4d4d4d}
  .tile.photo-kitchen{left:314px;top:248px;width:308px;height:169px;background:linear-gradient(135deg,#6b4a2e,#a6784c 45%,#d9c2a0 80%,#8b6a48)}
  .tile.photo-office{left:0;top:423px;width:127px;height:173px;background:linear-gradient(160deg,#2d2a26,#6a5e4d 55%,#c9b594)}
  .tile.photo-dining{left:131px;top:423px;width:175px;height:173px;background:linear-gradient(150deg,#c7b69b,#8c6a46 50%,#e2d6c2)}
  .tile.brand{left:316px;top:423px;width:177px;height:173px;background:var(--teal);display:flex;align-items:center;justify-content:center}
  .brand-name{display:flex;align-items:center;gap:8px;color:var(--paper);font-weight:400;font-size:22px;line-height:1}
  .brand-name .dot{width:12px;height:12px;background:var(--paper)}
  .cover-url{position:absolute;left:0;right:0;top:808px;text-align:center;font-size:22px;letter-spacing:.5px;color:#333}

  /* ---------- Product table ---------- */
  .range{top:1043px;height:900px;background:linear-gradient(180deg,#e8e8e8 0%,#f6f6f6 30%,#ffffff 100%)}
  .range-title{position:absolute;left:0;right:0;top:36px;text-align:center;font-size:25px;font-weight:700;color:var(--teal);letter-spacing:.5px}
  .spec-table{position:absolute;left:14px;top:82px;width:594px;height:600px;border:2px solid var(--teal);border-radius:18px;background:var(--paper);overflow:hidden;display:grid;grid-template-columns:48px repeat(5,1fr);grid-template-rows:117px 77px 78px 79px 96px 1fr}
  .row-label{background:var(--teal);color:var(--paper);display:flex;align-items:center;justify-content:center;border-bottom:1px solid rgba(255,255,255,.6)}
  .row-label span{transform:rotate(-90deg);font-size:15px;white-space:nowrap}
  .cell{border-left:1px solid var(--grid);border-bottom:1px solid var(--grid);display:flex;align-items:center;justify-content:center;text-align:center;font-size:11px;line-height:1.35;color:#444;padding:4px}
  .spec-table > :nth-last-child(-n+6){border-bottom:none}
  .product-shot{width:72px;height:80px;border-radius:6px;background:radial-gradient(circle at 50% 45%,#ffffff 0%,#d9dcdc 60%,#9ea3a3 100%)}
  .price-tab{position:absolute;left:181px;top:731px;width:258px;height:28px;background:var(--teal);color:var(--paper);font-size:16px;display:flex;align-items:center;justify-content:center;border-radius:4px 4px 0 0}
  .price-panel{position:absolute;left:18px;top:759px;width:590px;height:95px;background:var(--panel-dark);border:3px solid var(--teal);border-radius:16px;display:grid;grid-template-columns:1fr 1fr;align-content:center;row-gap:8px;padding:0 34px;color:var(--paper);font-size:20px}
  .price-panel .tier{white-space:nowrap}
  .price-panel .tier.right{padding-left:110px}
  .price-panel .amount{color:var(--teal-soft)}
  .range-url{position:absolute;right:20px;top:866px;font-size:14px;color:#444}

  /* ---------- Back cover ---------- */
  .back{top:2027px;height:878px;background:var(--teal)}
  .back-strip{position:absolute;left:0;top:0;width:100%;height:14px;background:#9a9a9a}
  .back-backdrop{position:absolute;left:0;top:14px;right:0;bottom:0;background:linear-gradient(180deg,#14b3a6 0%,#00a99d 40%,#0a978c 75%,#00a99d 100%)}
  .back-brand{position:absolute;left:0;right:0;top:300px;display:flex;justify-content:center}
  .back-brand .brand-name{font-size:32px;gap:12px}
  .back-brand .dot{width:16px;height:16px}
  .back-url{position:absolute;left:0;right:0;top:824px;text-align:center;font-size:21px;font-weight:600;color:var(--paper);letter-spacing:.5px}
</style>
</head>
<body>

<section class="page cover">
  <div class="cover-backdrop" role="img" aria-label="Faded bright kitchen interior with downlights"></div>
  <h1 class="cover-title"><span class="word">CATALOG</span><span class="years">2017-2018</span></h1>
  <div class="tile dark"></div>
  <div class="tile photo-kitchen" role="img" aria-label="Timber kitchen lit by LED downlights"></div>
  <div class="tile photo-office" role="img" aria-label="Boardroom ceiling with rows of downlights"></div>
  <div class="tile photo-dining" role="img" aria-label="Dining room and kitchen with recessed lighting"></div>
  <div class="tile brand"><div class="brand-name"><span class="dot"></span>brinholt electrical</div></div>
  <p class="cover-url">www.brinholt.com.au</p>
</section>

<section class="page range">
  <h2 class="range-title">CHOOSE YOUR STYLE OF LED DOWNLIGHTS</h2>
  <div class="spec-table">
    <div class="row-label"><span>Picture</span></div>
    <div class="cell"><div class="product-shot" role="img" aria-label="White round LED downlight"></div></div>
    <div class="cell"><div class="product-shot" role="img" aria-label="White LED downlight with driver"></div></div>
    <div class="cell"><div class="product-shot" role="img" aria-label="Black adjustable LED downlight"></div></div>
    <div class="cell"><div class="product-shot" role="img" aria-label="Satin chrome LED downlight"></div></div>
    <div class="cell"><div class="product-shot" role="img" aria-label="LED driver unit"></div></div>

    <div class="row-label"><span>Brand</span></div>
    <div class="cell">Brand of<br>Downlight</div><div class="cell">Brand of<br>Downlight</div><div class="cell">Brand of<br>Downlight</div><div class="cell">Brand of<br>Downlight</div><div class="cell">Brand of<br>Downlight</div>

    <div class="row-label"><span>Watts</span></div>
    <div class="cell">Watt of light<br>(9w etc)</div><div class="cell">Watt of light<br>(9w etc)</div><div class="cell">Watt of light<br>(9w etc)</div><div class="cell">Watt of light<br>(9w etc)</div><div class="cell">Watt of light<br>(9w etc)</div>

    <div class="row-label"><span>Lumen</span></div>
    <div class="cell">Lumen out put<br>(800lm etc)</div><div class="cell">Lumen out put<br>(800lm etc)</div><div class="cell">Lumen out put<br>(800lm etc)</div><div class="cell">Lumen out put<br>(800lm etc)</div><div class="cell">Lumen out put<br>(800lm etc)</div>

    <div class="row-label"><span>Warranty</span></div>
    <div class="cell">Warranty<br>(7 Years etc)</div><div class="cell">Warranty<br>(7 Years etc)</div><div class="cell">Warranty<br>(7 Years etc)</div><div class="cell">Warranty<br>(7 Years etc)</div><div class="cell">Warranty<br>(7 Years etc)</div>

    <div class="row-label"><span>Price</span></div>
    <div class="cell">Special offer<br>(given below)</div><div class="cell">Special offer<br>(given below)</div><div class="cell">Special offer<br>(given below)</div><div class="cell">Special offer<br>(given below)</div><div class="cell">Special offer<br>(given below)</div>
  </div>

  <div class="price-tab">Quarnel Ostrava 9w LED</div>
  <div class="price-panel">
    <div class="tier">1-10......lights : <span class="amount">$49</span></div>
    <div class="tier right">21-40...lights : <span class="amount">$42</span></div>
    <div class="tier">11-20...lights : <span class="amount">$45</span></div>
    <div class="tier right">40 and over : <span class="amount">$40</span></div>
  </div>
  <p class="range-url">www.brinholt.com.au</p>
</section>

<section class="page back">
  <div class="back-strip"></div>
  <div class="back-backdrop" role="img" aria-label="Teal-toned bedroom interior with ceiling downlights"></div>
  <div class="back-brand"><div class="brand-name"><span class="dot"></span>brinholt electrical</div></div>
  <p class="back-url">www.brinholt.com.au</p>
</section>

</body>
</html>
```